Harborline Auto LLC

Car Dealer Customer Service
Address: 2874 Cresthaven Road, Dunmore Hollow, KY 40999
web: www.harborlineautoxq.net
email: harborlineautoxq@mailnest.example
Phone: (555) 555-0148
Phone: (555) 555-0173

```html
<!DOCTYPE html>
<html lang="en">
<head>
<meta charset="utf-8">
<title>Harborline Auto LLC – Business Card</title>
<link rel="stylesheet" href="https://fonts.googleapis.com/css2?family=Montserrat:wght@700;800&family=Roboto:wght@400;500&display=swap">
<style>
  :root {
    --bg: #3a3a3a;
    --card: #1b1b1c;
    --card-back: #161617;
    --blue: #2a8fd0;
    --gold: #f0b33c;
    --white: #f2f2f2;
    --emboss: #2a2a2c;
  }
  * { box-sizing: border-box; margin: 0; padding: 0; }
  html, body { width: 1200px; height: 801px; overflow: hidden; }
  body {
    background: var(--bg);
    font-family: "Roboto", Arial, sans-serif;
    display: flex;
    align-items: center;
    justify-content: center;
    gap: 40px;
  }
  .card {
    position: relative;
    width: 520px;
    height: 297px;
    background: var(--card);
    border-bottom: 3px solid var(--blue);
    box-shadow: 0 10px 28px rgba(0,0,0,.45);
  }
  .card--front { display: flex; }
  .brand-panel {
    width: 235px;
    display: flex;
    align-items: center;
    justify-content: center;
    gap: 12px;
  }
  .brand-dot {
    width: 40px; height: 40px;
    border-radius: 50%;
    background: var(--gold);
    flex: none;
  }
  .brand-name {
    font-family: "Montserrat", Arial, sans-serif;
    font-weight: 800;
    font-size: 22px;
    line-height: 1.05;
    color: var(--blue);
    text-transform: uppercase;
    letter-spacing: .5px;
  }
  .divider {
    width: 1.5px;
    background: var(--blue);
    margin: 78px 0 70px;
  }
  .contact {
    padding: 76px 0 0 20px;
    color: var(--white);
    font-size: 13.5px;
    line-height: 1.38;
  }
  .contact-title { color: var(--blue); font-weight: 500; font-size: 14.5px; }
  .contact-address { margin-bottom: 8px; }
  .contact-line { display: flex; align-items: center; gap: 7px; white-space: nowrap; }
  .contact-line svg { width: 11px; height: 11px; fill: var(--gold); flex: none; }
  .card--back {
    background: var(--card-back);
    display: flex;
    align-items: center;
    justify-content: center;
  }
  .back-name {
    font-family: "Montserrat", Arial, sans-serif;
    font-weight: 800;
    font-size: 28px;
    color: var(--emboss);
    text-transform: uppercase;
    letter-spacing: 1px;
  }
</style>
</head>
<body>
  <section class="card card--front" aria-label="Business card front">
    <div class="brand-panel">
      <span class="brand-dot"></span>
      <span class="brand-name">Harborline<br>Auto</span>
    </div>
    <div class="divider"></div>
    <div class="contact">
      <p class="contact-title">Car Dealer Customer Service</p>
      <p class="contact-address">2874 Cresthaven Road<br>Dunmore Hollow, KY 40999</p>
      <p class="contact-line"><svg viewBox="0 0 24 24"><path d="M6.6 10.8a15.2 15.2 0 0 0 6.6 6.6l2.2-2.2c.3-.3.7-.4 1-.2 1.1.4 2.3.6 3.6.6.6 0 1 .4 1 1V20c0 .6-.4 1-1 1A17 17 0 0 1 3 4c0-.6.4-1 1-1h3.5c.6 0 1 .4 1 1 0 1.3.2 2.5.6 3.6.1.3 0 .7-.2 1z"/></svg>(555) 555-0148</p>
      <p class="contact-line"><svg viewBox="0 0 24 24"><path d="M6.6 10.8a15.2 15.2 0 0 0 6.6 6.6l2.2-2.2c.3-.3.7-.4 1-.2 1.1.4 2.3.6 3.6.6.6 0 1 .4 1 1V20c0 .6-.4 1-1 1A17 17 0 0 1 3 4c0-.6.4-1 1-1h3.5c.6 0 1 .4 1 1 0 1.3.2 2.5.6 3.6.1.3 0 .7-.2 1z"/></svg>(555) 555-0173</p>
      <p class="contact-line"><svg viewBox="0 0 24 24"><path d="M2 5h20v14H2zm2 2v.5l8 5 8-5V7l-8 5z"/></svg>harborlineautoxq@mailnest.example</p>
      <p class="contact-line"><svg viewBox="0 0 24 24"><path d="M12 2a10 10 0 1 0 0 20 10 10 0 0 0 0-20zm0 2c1 0 2.3 2 2.8 5H9.2C9.7 6 11 4 12 4zm-7.7 7h3.1a17 17 0 0 0 0 2H4.3a8 8 0 0 1 0-2zm5 0h5.4a15 15 0 0 1 0 2H9.3a15 15 0 0 1 0-2zm7.3 0h3.1a8 8 0 0 1 0 2h-3.1a17 17 0 0 0 0-2zM9.2 15h5.6c-.5 3-1.8 5-2.8 5s-2.3-2-2.8-5z"/></svg>www.harborlineautoxq.net</p>
    </div>
  </section>

  <section class="card card--back" aria-label="Business card back">
    <span class="back-name">Harborline Auto</span>
  </section>
</body>
</html>
```